Fun Employee News and Engagement Portal - Tidy Hearth Company

We are looking for a clean, but fun WordPress template for an internal employee engagement website. The site will be a place we share news, fun stories and pictures. We'll provide space for our employees to post comments, etc.
We are a deep dish pizza restaurant with a rich history. I'd love to see your take on a look and feel for us! The site will be called Bim-Zee. I've posted some images and colors along with this brief description.
Focus on making the template whimsical and fun! (Extra point for focusing on the "Lettering in lights" ).
I will continue to post additional pieces of art and content examples.
Reason: Our team is continuing to review designs. We've decided to extend the timing a few more days. Good luck! Make it playful!
Reason: We need more time with our team to review these designs. We are going to extend one more time!
Reason: Still trying to get enough time to review with the Bim-Zee team!
Reason: We are continuing to evaluate designs. Thank you!
Industry/Entity Type
American Restaurant
Number of Pages Required
1 page
Look and feel
Each slider illustrates characteristics of the customer's brand and the style your logo design should communicate.

```html
<!DOCTYPE html>
<html lang="en">
<head>
<meta charset="utf-8">
<title>Bim-Zee — Tidy Hearth Company</title>
<link href="https://fonts.googleapis.com/css2?family=Lobster&family=Open+Sans:wght@400;600;700&display=swap" rel="stylesheet">
<style>
  :root{
    --red:#d92a2e;
    --ink:#333333;
    --muted:#666666;
    --rule:#e2e2e2;
    --band:#f7f7f7;
    --white:#ffffff;
    --crust:#8a5a34;
    --tomato:#b8322a;
    --basil:#3e6a2c;
  }
  *{box-sizing:border-box;margin:0;padding:0}
  html,body{width:1200px;height:3072px;overflow:hidden}
  body{position:relative;font-family:"Open Sans",Arial,sans-serif;color:var(--ink);background:var(--white)}
  .abs{position:absolute}
  .script{font-family:"Lobster",cursive}

  /* Hero */
  .hero{left:0;top:0;width:1200px;height:580px}
  .hero-photo{position:absolute;inset:0;background:
      radial-gradient(ellipse at 30% 60%, #c98a3e 0%, transparent 45%),
      radial-gradient(ellipse at 80% 30%, #9c2a1f 0%, transparent 40%),
      radial-gradient(ellipse at 60% 85%, #5b7a2e 0%, transparent 40%),
      linear-gradient(135deg,#5a3520,#7b4a2a 45%,#3e2416)}
  .hero-shade{position:absolute;inset:0;background:rgba(20,12,8,.35)}
  .brand{left:155px;top:26px;font-size:40px;color:var(--white)}
  .nav{right:143px;top:36px;display:flex;gap:34px}
  .nav a{font-family:"Lobster",cursive;font-size:21px;color:var(--white);text-decoration:none}
  .nav a.active{color:var(--red)}
  .hero-title{left:0;width:1200px;top:250px;text-align:center;font-size:48px;color:var(--white)}
  .hero-sub{left:0;width:1200px;top:322px;text-align:center;font-size:16px;color:#eee}
  .hero-btn{left:499px;top:380px;width:202px;height:48px;border:2px solid var(--white);border-radius:24px;color:var(--white);font-size:14px;font-weight:600;letter-spacing:1px;display:flex;align-items:center;justify-content:center}
  .dots{left:584px;top:506px;display:flex;gap:10px}
  .dots span{width:8px;height:8px;border-radius:50%;background:var(--white)}

  /* Section headers */
  .section-title{left:0;width:1200px;text-align:center;font-size:56px;color:var(--red)}
  .rule{left:143px;width:914px;height:2px;background:var(--rule)}

  /* News */
  .card{width:288px}
  .card-img{width:288px;height:168px}
  .card-meta{margin-top:28px;font-size:12px;font-weight:700;color:var(--ink)}
  .card-head{margin-top:16px;font-family:"Lobster",cursive;font-size:14px;color:var(--red)}
  .card-text{margin-top:6px;font-size:13px;line-height:24px;color:var(--ink)}
  .card-foot{margin-top:22px;display:flex;align-items:center;gap:16px}
  .pill{width:98px;height:30px;border:2px solid var(--red);border-radius:15px;font-size:10px;font-weight:600;display:flex;align-items:center;justify-content:center}
  .share{font-size:10px;font-weight:700;display:flex;align-items:center;gap:10px}
  .share i{width:7px;height:7px;border-radius:50%;background:var(--red);display:block}
  .share i.alt{background:#9bb8d3}

  /* Stories */
  .stories{left:0;top:1160px;width:1200px;height:537px;background:var(--band)}
  .story-deco{left:690px;top:1265px;width:540px;height:360px;border-radius:50%;background:radial-gradient(ellipse,#e4e4e4 0%,transparent 70%)}
  .avatar{left:166px;top:1356px;width:246px;height:246px;border:8px solid var(--red);border-radius:50%;background:var(--white);padding:12px}
  .avatar div{width:100%;height:100%;border-radius:50%;background:linear-gradient(160deg,#c9d6e2,#9fb2c4 60%,#b6473d)}
  .quote-mark{left:436px;top:1382px;font-family:"Lobster",cursive;font-size:92px;line-height:1;color:var(--red)}
  .story-name{left:502px;top:1400px;font-size:28px;color:var(--ink)}
  .story-text{left:438px;top:1456px;width:560px;font-size:15px;line-height:28px;color:var(--muted)}
  .arrows{left:582px;top:1600px}

  /* Gallery */
  .tile{width:288px;height:187px}
  .tile-brand{display:flex;flex-direction:column;align-items:center;justify-content:center;color:var(--white)}
  .tile-brand .script{font-size:36px}
  .tile-brand p{font-size:11px;margin-top:4px}

  /* Comment */
  .comment-box{left:143px;top:2497px;width:914px;height:141px;border:1px solid var(--rule);border-radius:4px;padding:22px 16px;font-size:17px;color:#999}
  .send-btn{left:139px;top:2656px;width:154px;height:44px;background:var(--red);color:var(--white);border-radius:3px;font-size:17px;display:flex;align-items:center;justify-content:center}

  /* Footer */
  .footer{left:0;top:2750px;width:1200px;height:260px;background:var(--band)}
  .foot-brand{left:155px;top:2776px;font-size:38px;color:var(--red)}
  .foot-label{left:166px;top:2857px;font-size:11px;font-weight:600}
  .badge{left:166px;width:110px;height:36px;border-radius:4px;background:var(--red)}
  .badge.dark{background:#3a3a3a;border-radius:18px;width:100px}
  .foot-col{top:2802px}
  .foot-col h4{font-family:"Lobster",cursive;font-weight:400;font-size:14px;color:var(--red);margin-bottom:22px}
  .foot-col li{list-style:none;font-size:12px;line-height:24px}
  .bottom-bar{left:0;top:3010px;width:1200px;height:62px;border-top:1px solid var(--rule);display:flex;align-items:center;justify-content:center;font-size:12px}
</style>
</head>
<body>

<header class="hero abs">
  <div class="hero-photo" role="img" aria-label="Photo of a pizza with basil, peppers and tomatoes on a wooden table"></div>
  <div class="hero-shade"></div>
</header>
<div class="brand abs script">Bim-Zee</div>
<nav class="nav abs">
  <a class="active">Home</a><a>About Us</a><a>News</a><a>Stories</a><a>Gallery</a><a>Contact Us</a>
</nav>
<h1 class="hero-title abs script" style="font-weight:400">We are a tidy hearth company</h1>
<p class="hero-sub abs">Neque porro quisquam est qui dolorem ipsum quia dolor sit amet, consectetur...</p>
<div class="hero-btn abs">LEARN MORE</div>
<div class="dots abs"><span></span><span></span><span></span></div>

<!-- News -->
<h2 class="section-title abs script" style="top:618px;font-weight:400">News</h2>
<div class="rule abs" style="top:705px"></div>

<article class="card abs" style="left:143px;top:757px">
  <div class="card-img" role="img" aria-label="Photo of a pizza with tomatoes and herbs" style="background:linear-gradient(135deg,#6b3b1e,#c5632e 50%,#8a2b1c)"></div>
  <div class="card-meta">POSTED BY FEBRUARY 2017</div>
  <div class="card-head">Sed ut perspiciatis unde omnis iste natus</div>
  <p class="card-text">Doloremque laudantium, totam rem aperiam, eaque ipsa quae ab illo inventore veritatis et</p>
  <div class="card-foot"><div class="pill">READ MORE</div><div class="share">SHARE <i></i><i class="alt"></i></div></div>
</article>
<article class="card abs" style="left:456px;top:757px">
  <div class="card-img" role="img" aria-label="Photo of friends laughing while eating pizza" style="background:linear-gradient(135deg,#4f7d9c,#d8b28a 55%,#6d9a57)"></div>
  <div class="card-meta">POSTED BY FEBRUARY 2017</div>
  <div class="card-head">Sed ut perspiciatis unde omnis iste natus</div>
  <p class="card-text">Doloremque laudantium, totam rem aperiam, eaque ipsa quae ab illo inventore veritatis et</p>
  <div class="card-foot"><div class="pill">READ MORE</div><div class="share">SHARE <i></i><i class="alt"></i></div></div>
</article>
<article class="card abs" style="left:769px;top:757px">
  <div class="card-img" role="img" aria-label="Photo of a pizza with olives and peppers" style="background:linear-gradient(135deg,#c24a2a,#e39a4a 50%,#7a3a1c)"></div>
  <div class="card-meta">POSTED BY FEBRUARY 2017</div>
  <div class="card-head">Sed ut perspiciatis unde omnis iste natus</div>
  <p class="card-text">Doloremque laudantium, totam rem aperiam, eaque ipsa quae ab illo inventore veritatis et</p>
  <div class="card-foot"><div class="pill">READ MORE</div><div class="share">SHARE <i></i><i class="alt"></i></div></div>
</article>

<!-- Fun Stories -->
<section class="stories abs"></section>
<div class="story-deco abs" role="img" aria-label="Faint illustration of a pizza on a serving paddle"></div>
<h2 class="section-title abs script" style="top:1213px;font-weight:400">Fun Stories</h2>
<div class="rule abs" style="top:1300px"></div>
<div class="avatar abs"><div role="img" aria-label="Portrait photo of a smiling team member"></div></div>
<div class="quote-mark abs">“</div>
<div class="story-name abs">Milo Brandt</div>
<p class="story-text abs">Sed ut perspiciatis unde omnis iste natus error sit voluptatem accusantium doloremque laudantium, totam rem aperiam, eaque ipsa quae ab illo inventore veritatis et quasi architecto beatae vitae dicta sunt explicabo. Nemo enim ipsam voluptatem quia voluptas sit aspernatur aut odit aut</p>
<svg class="arrows abs" width="36" height="24" viewBox="0 0 36 24" aria-hidden="true">
  <polyline points="12,4 4,12 12,20" fill="none" stroke="#555" stroke-width="2"/>
  <polyline points="24,4 32,12 24,20" fill="none" stroke="#555" stroke-width="2"/>
</svg>

<!-- Gallery -->
<h2 class="section-title abs script" style="top:1733px;font-weight:400">Gallery</h2>
<div class="rule abs" style="top:1823px"></div>
<div class="tile tile-brand abs" style="left:143px;top:1886px;background:linear-gradient(135deg,#5a3a24,#8a5a34 55%,#4a2e1c)" role="img" aria-label="Dimmed pizza photo with site name">
  <span class="script">Bim-Zee</span><p>Neque porro quisquam, consectetur...</p>
</div>
<div class="tile abs" style="left:456px;top:1886px;background:linear-gradient(135deg,#4f6b3a,#c99a6a 55%,#6a4a2a)" role="img" aria-label="Photo of a couple sharing pizza"></div>
<div class="tile abs" style="left:769px;top:1886px;background:linear-gradient(135deg,#d46a3a,#e8b06a 50%,#8a3a22)" role="img" aria-label="Photo of pizzas on a table"></div>
<div class="tile abs" style="left:143px;top:2103px;background:linear-gradient(135deg,#2a2a2a,#a2502a 55%,#2f2f2f)" role="img" aria-label="Photo of a sliced pizza on a dark board"></div>
<div class="tile abs" style="left:456px;top:2103px;background:linear-gradient(135deg,#3a2a1e,#b27a48 55%,#4a3020)" role="img" aria-label="Photo of friends eating pizza at a bar"></div>
<div class="tile abs" style="left:769px;top:2103px;background:linear-gradient(135deg,#e0b48a,#c46a34 55%,#f0d2b0)" role="img" aria-label="Photo of hands reaching for pizza slices"></div>

<!-- Post Comment -->
<h2 class="section-title abs script" style="top:2366px;font-weight:400">Post Comment</h2>
<div class="rule abs" style="top:2460px"></div>
<div class="comment-box abs">Post Your Comment</div>
<div class="send-btn abs">SEND POST</div>

<!-- Footer -->
<footer class="footer abs"></footer>
<div class="foot-brand abs script">Bim-Zee</div>
<div class="foot-label abs">ASSOCIATED LOGOS</div>
<div class="badge abs" style="top:2880px" role="img" aria-label="Partner badge"></div>
<div class="badge dark abs" style="top:2934px" role="img" aria-label="Partner badge"></div>

<div class="foot-col abs" style="left:371px">
  <h4>Quick Links</h4>
  <ul><li>Home</li><li>About Us</li><li>News</li><li>Stories</li><li>Gallery</li><li>Contact Us</li></ul>
</div>
<div class="foot-col abs" style="left:588px">
  <h4>Other Links</h4>
  <ul><li>Terms Of Service</li><li>Privacy Policy</li><li>Help</li></ul>
</div>
<div class="foot-col abs" style="left:770px">
  <h4>Contact Us</h4>
  <ul><li>Hearthside Office</li><li>Ember Lane 12</li><li>60601 Oakfield</li><li>&nbsp;</li><li>E-Mail: hello@bimzee-team.com</li></ul>
</div>

<div class="bottom-bar abs">© 2017 Company Name &nbsp;|&nbsp; All Rights Reserved</div>

</body>
</html>
```